Request for Business Card Design

Hi. My name is Marlene, I am looking for a new business card design for my company, Quarrow Signal Instruments, LLC. I really like the design you did for Tarsel Venture and was hoping you could do something similar using our full logo and our mark. I am also open to any raised texture design using our mark. I have attached our full logo, which would need to be somewhere on the card, as well as the mark in both outline and full form, as well as our brand colors / guide. The card does not have to be white, as long as our logo and mark appear. I actually like darker colored business cards more, but am open to all options. If you are interested in working with me, please let me know. We would also take the business card design into letterhead design if you can do that.

```html
<!DOCTYPE html>
<html lang="en">
<head>
<meta charset="UTF-8">
<title>Quarrow Signal Instruments — Business Card</title>
<link href="https://fonts.googleapis.com/css2?family=Montserrat:wght@400;500;700;800&display=swap" rel="stylesheet">
<style>
  :root {
    --stage: #1c1c1e;
    --card: #161616;
    --ink: #ffffff;
    --ink-soft: #d8d8d8;
    --accent: #1a9fd0;
    --relief-light: #6e6e72;
    --relief-dark: #1f1f21;
  }
  * { box-sizing: border-box; margin: 0; padding: 0; }
  html, body {
    width: 1200px; height: 900px; overflow: hidden;
    background: var(--stage);
    font-family: "Montserrat", sans-serif;
  }
  .stage {
    width: 1200px; height: 900px;
    display: flex; align-items: center; justify-content: center; gap: 40px;
  }
  .card {
    position: relative;
    width: 540px; height: 309px;
    background: var(--card);
    border-radius: 18px;
    overflow: hidden;
    box-shadow: 0 18px 40px rgba(0,0,0,.45);
  }

  /* Brand lockup */
  .brand {
    position: absolute;
    display: flex; align-items: center; gap: 12px;
  }
  .brand-dot {
    width: 34px; height: 34px; border-radius: 50%;
    background: var(--accent); flex: none;
  }
  .brand-name {
    color: var(--ink);
    font-weight: 800;
    font-size: 17px;
    line-height: 1.15;
    letter-spacing: .06em;
    text-transform: uppercase;
    width: 190px;
  }

  /* Front */
  .card-front .brand { left: 34px; top: 124px; }
  .divider {
    position: absolute; left: 272px; top: 70px;
    width: 1.5px; height: 170px; background: var(--accent);
  }
  .contact { position: absolute; left: 296px; top: 70px; color: var(--ink); }
  .contact-name {
    color: var(--accent); font-weight: 700; font-size: 22px; line-height: 1.1;
  }
  .contact-role { font-size: 13px; font-weight: 500; margin-bottom: 12px; }
  .contact-list { list-style: none; font-size: 11.5px; line-height: 1.7; color: var(--ink-soft); }
  .contact-list li { display: flex; align-items: center; gap: 8px; }
  .contact-list svg { width: 11px; height: 11px; fill: var(--accent); flex: none; }
  .address { margin-top: 10px; font-size: 11.5px; line-height: 1.5; color: var(--ink-soft); }

  /* Back */
  .relief {
    position: absolute; left: -60px; top: 90px;
    width: 330px; height: 330px; border-radius: 50%;
    background: radial-gradient(circle at 65% 35%, var(--relief-light) 0%, #3a3a3d 35%, var(--relief-dark) 70%);
    opacity: .9;
  }
  .card-back .brand { right: 28px; bottom: 60px; }
</style>
</head>
<body>
<main class="stage">
  <section class="card card-front" aria-label="Card front">
    <div class="brand">
      <span class="brand-dot"></span>
      <span class="brand-name">Quarrow Signal Instruments</span>
    </div>
    <div class="divider"></div>
    <div class="contact">
      <p class="contact-name">Marlene Hadley</p>
      <p class="contact-role">Owner</p>
      <ul class="contact-list">
        <li><svg viewBox="0 0 24 24"><path d="M6.6 10.8a15 15 0 0 0 6.6 6.6l2.2-2.2a1 1 0 0 1 1-.25 11.4 11.4 0 0 0 3.6.57 1 1 0 0 1 1 1V20a1 1 0 0 1-1 1A17 17 0 0 1 3 4a1 1 0 0 1 1-1h3.5a1 1 0 0 1 1 1c0 1.25.2 2.45.57 3.6a1 1 0 0 1-.25 1z"/></svg>+001 303 555 0142</li>
        <li><svg viewBox="0 0 24 24"><path d="M2 5h20v14H2zm2 2v.5l8 5 8-5V7l-8 5z"/></svg>info@quarrowsignal.com</li>
        <li><svg viewBox="0 0 24 24"><path d="M12 2a10 10 0 1 0 0 20 10 10 0 0 0 0-20zm0 2c1 1.3 1.8 3 2.1 5H9.9C10.2 7 11 5.3 12 4zm-8 8h3.9a16 16 0 0 0 .2 1.5H4.2A8 8 0 0 1 4 12zm8 8c-1-1.3-1.8-3-2.1-5h4.2c-.3 2-1.1 3.7-2.1 5zm4.1-7H19.8a8 8 0 0 1-.2 1.5h-3.7z"/></svg>www.quarrowsignal.com</li>
      </ul>
      <p class="address">1180 Meridian Park Way<br>Loveland, CO 80538</p>
    </div>
  </section>

  <section class="card card-back" aria-label="Card back">
    <div class="relief" role="img" aria-label="Raised texture area for the brand mark"></div>
    <div class="brand">
      <span class="brand-dot"></span>
      <span class="brand-name">Quarrow Signal Instruments</span>
    </div>
  </section>
</main>
</body>
</html>
```